Fresh Dwelling Tract Guide needs a new Landing Page

I like to get a landing page or website with 2-3 pages to help target home buyers who are looking to buy homes from builders such as TW Residences, Morvik, P.L. Fennick, etc. The landing page/website to be non-cluttered and be able to explain to home buyers that there are many benefits to include me as their buyer's agent when they buy a brand new home from any builders.
I may want to incorporate a short explanation video (animated) on the landing page and then for the viewer to click on a button that will take them to another page where they can search for new homes from different builders.
Target Market(s)
Home buyers looking to buy brand new home from builders such as TW Residences, Morvik, P.L. Fennick, etc.
Industry/Entity Type
Real Estate
Number of Pages Required
2 page
Font styles to use
Requirements
Must have
- The landing page may have the explanation video at the bottom of the landing page (scrolled down) or there may be a CALL TO ACTION button that takes the viewer to the 2nd page to watch the explanation video. Once they watched the explanation video and are still interested, they can click on another CALL TO ACTION button that will take them to another website that they will be able to search for all the available new homes and register their contact information.
Should not have
- No clutters and no dark colors.

```html
<!DOCTYPE html>
<html lang="en">
<head>
<meta charset="utf-8">
<title>Fresh Dwelling Tract Guide</title>
<link rel="stylesheet" href="https://fonts.googleapis.com/css2?family=Lora:ital,wght@1,400&family=Open+Sans:wght@400;600;700&family=Kaushan+Script&family=Libre+Baskerville&display=swap">
<style>
  :root {
    --brown: #5a4630;
    --green: #a8b845;
    --band: #f4f4f4;
    --white: #ffffff;
    --placeholder: #a9a39a;
    --photo-gray: #7a7a7a;
    --photo-warm: #b9a58d;
  }
  * { margin: 0; padding: 0; box-sizing: border-box; }
  html, body { width: 1200px; height: 1200px; overflow: hidden; background: var(--white); }
  body { position: relative; font-family: "Open Sans", sans-serif; color: var(--brown); }

  .testimonial { position: absolute; left: 0; top: 0; width: 1200px; height: 308px; background: var(--band); }
  .slider-arrow { position: absolute; top: 52px; width: 24px; height: 36px; }
  .slider-arrow.prev { left: 82px; }
  .slider-arrow.next { left: 1092px; }
  .client-photo {
    position: absolute; left: 174px; top: -16px; width: 172px; height: 172px; border-radius: 50%;
    background: radial-gradient(circle at 50% 40%, #b5b5b5, #5c5c5c 70%, #2e2e2e);
    box-shadow: 0 3px 8px rgba(0,0,0,.15);
  }
  .quote-mark { position: absolute; left: 436px; top: 6px; font-family: "Lora", serif; font-style: italic; font-size: 64px; line-height: 1; color: var(--brown); }
  .quote-text { position: absolute; left: 433px; top: 78px; width: 600px; font-family: "Lora", serif; font-style: italic; font-size: 23px; line-height: 27px; }
  .quote-author { position: absolute; left: 433px; top: 167px; font-size: 15px; }
  .quote-author strong { font-weight: 700; }

  .hero-title { position: absolute; left: 0; top: 392px; width: 1200px; text-align: center; font-family: "Kaushan Script", cursive; font-size: 92px; line-height: 120px; color: var(--brown); }
  .cta-button {
    position: absolute; left: 509px; top: 549px; width: 182px; height: 54px; background: var(--green);
    color: var(--white); font-weight: 700; font-size: 14px; letter-spacing: 2px; text-align: center; line-height: 54px; border-radius: 2px;
  }
  .video-link { position: absolute; left: 490px; top: 655px; font-weight: 700; font-size: 15px; letter-spacing: 1.6px; }
  .play-icon { position: absolute; left: 680px; top: 645px; width: 42px; height: 42px; }

  .contact-heading { position: absolute; left: 88px; top: 800px; font-family: "Libre Baskerville", serif; font-size: 21px; }
  .contact-intro { position: absolute; left: 88px; top: 862px; width: 480px; font-size: 15px; line-height: 21px; }
  .field {
    position: absolute; left: 88px; width: 430px; height: 54px; background: var(--white);
    box-shadow: 0 1px 6px rgba(0,0,0,.08); padding-left: 28px; line-height: 54px;
    font-size: 12px; font-weight: 600; letter-spacing: 1.4px; color: var(--placeholder);
  }
  .agent-photo {
    position: absolute; left: 643px; top: 824px; width: 78px; height: 78px; border-radius: 50%;
    background: linear-gradient(180deg, #dcc6a6, var(--photo-warm) 55%, #4a4038);
    box-shadow: 0 3px 8px rgba(0,0,0,.18);
  }
  .agent-name { position: absolute; left: 759px; top: 822px; font-family: "Libre Baskerville", serif; font-size: 21px; }
  .agent-line { position: absolute; left: 759px; font-size: 15px; }
  .agent-contact { position: absolute; left: 788px; font-size: 15px; }
  .contact-icon { position: absolute; left: 761px; width: 16px; height: 16px; }
</style>
</head>
<body>
  <section class="testimonial">
    <svg class="slider-arrow prev" viewBox="0 0 24 36"><polyline points="20,3 5,18 20,33" fill="none" stroke="#a8b845" stroke-width="3.5"/></svg>
    <div class="client-photo" role="img" aria-label="Black and white portrait of a client"></div>
    <div class="quote-mark">&ldquo;</div>
    <p class="quote-text">Lorem ipsum dolor sit amet, consectetur adipisicing elit, sed do eiusmod</p>
    <p class="quote-author"><strong>Mira Castell</strong>, VP of Global Marketing, Verdalune</p>
    <svg class="slider-arrow next" viewBox="0 0 24 36"><polyline points="4,3 19,18 4,33" fill="none" stroke="#a8b845" stroke-width="3.5"/></svg>
  </section>

  <h1 class="hero-title">Find your home today</h1>
  <div class="cta-button">FIND A HOME</div>
  <div class="video-link">Watch how it works</div>
  <svg class="play-icon" viewBox="0 0 42 42"><circle cx="21" cy="21" r="19.5" fill="none" stroke="#5a4630" stroke-width="2"/><polygon points="16,13 29,21 16,29" fill="#5a4630"/></svg>

  <h2 class="contact-heading">GET IN TOUCH</h2>
  <p class="contact-intro">We're always available to help out, get in touch with us any time, or shoot us an email.</p>
  <div class="field" style="top:965px">First Name</div>
  <div class="field" style="top:1051px">Last Name</div>
  <div class="field" style="top:1138px">Email Address</div>

  <div class="agent-photo" role="img" aria-label="Photo of the agent standing outdoors at sunset"></div>
  <div class="agent-name">Your Name</div>
  <div class="agent-line" style="top:867px">CalDRE License # 09876543</div>
  <svg class="contact-icon" style="top:909px" viewBox="0 0 24 24"><path fill="#5a4630" d="M6.6 10.8c1.4 2.8 3.8 5.1 6.6 6.6l2.2-2.2c.3-.3.7-.4 1-.2 1.1.4 2.3.6 3.6.6.6 0 1 .4 1 1V20c0 .6-.4 1-1 1C10.6 21 3 13.4 3 4c0-.6.4-1 1-1h3.5c.6 0 1 .4 1 1 0 1.3.2 2.5.6 3.6.1.3 0 .7-.2 1z"/></svg>
  <div class="agent-contact" style="top:906px">555.014.2290</div>
  <svg class="contact-icon" style="top:942px" viewBox="0 0 24 24"><path fill="#5a4630" d="M20 4H4c-1.1 0-2 .9-2 2v12c0 1.1.9 2 2 2h16c1.1 0 2-.9 2-2V6c0-1.1-.9-2-2-2zm0 4l-8 5-8-5V6l8 5 8-5v2z"/></svg>
  <div class="agent-contact" style="top:939px">email me</div>
</body>
</html>
```